Stationery for a private security company, "Brenmoor Security Services Ltd."

Needed is a stationery design for a private security company. The designs must show professionalism and that our company mean nothing but business. Watermark of the company logo on the letterhead page is also a must. The final design must represent innovation and professionalism. It would be great if designers could integrate the colours black and silver onto the cards and letterheads..

Thank you

```html
<!DOCTYPE html>
<html lang="en">
<head>
<meta charset="utf-8">
<title>Brenmoor Security Services Ltd. — Stationery</title>
<link rel="stylesheet" href="https://fonts.googleapis.com/css2?family=Open+Sans:wght@400;600&display=swap">
<style>
:root{
  --bg:#ececec;
  --paper:#ffffff;
  --ink:#111111;
  --band:#0d0d0d;
  --silver:#9d9d9d;
  --silver-light:#c4c4c4;
  --text:#444444;
}
*{margin:0;padding:0;box-sizing:border-box}
html,body{width:1200px;height:937px;overflow:hidden;background:var(--bg)}
body{position:relative;font-family:"Open Sans",Arial,sans-serif;color:var(--ink)}
.piece{position:absolute;background:var(--paper);overflow:hidden}
.frame{position:absolute;border:3px solid var(--silver);border-bottom:none}
.band{position:absolute;left:0;right:0;bottom:0;background:var(--band);color:#fff;display:flex;align-items:center;justify-content:flex-end;letter-spacing:.08em}
.band svg{position:absolute;left:0;bottom:0}
.band span{position:relative}

/* wordmark */
.brand{position:absolute;display:flex;align-items:center;gap:6px;font-weight:600;color:var(--ink);text-transform:uppercase}
.brand-dot{border-radius:50%;background:var(--ink);flex:none}
.brand-text{line-height:1.05}
.brand-text b{display:block;font-weight:600;letter-spacing:.06em}
.brand-text i{display:block;font-style:normal;font-weight:600;letter-spacing:.02em}

/* letterhead */
.letterhead{left:185px;top:66px;width:388px;height:546px}
.letterhead .frame{left:9px;top:14px;right:9px;bottom:27px}
.letterhead .band{height:27px;font-size:12.5px;padding-right:22px}
.letter{position:absolute;left:36px;top:140px;width:300px;font-size:5.6px;line-height:8px;color:var(--text)}
.letter p{margin-bottom:8px}
.letter .gap{margin-bottom:20px}
.signature{width:38px;height:18px;background:linear-gradient(90deg,#bbb,#888);border-radius:2px;margin:4px 0 6px}
.letter strong{color:var(--ink);font-weight:600}

/* blank second sheet */
.sheet{left:636px;top:41px;width:458px;height:575px}
.sheet .frame{left:20px;top:18px;right:20px;bottom:37px}
.sheet .band{height:37px;font-size:15px;justify-content:center}

/* business cards */
.card{left:45px;width:176px}
.card-front{top:661px;height:97px}
.card-front .frame{left:6px;top:6px;right:6px;bottom:9px}
.card-front .band{height:9px}
.card-name{position:absolute;right:14px;top:13px;text-align:right;font-size:7.5px;line-height:9px}
.card-name small{display:block;font-size:5.5px;color:var(--text)}
.contacts{position:absolute;left:12px;top:58px;width:154px;display:grid;grid-template-columns:1fr 1fr;gap:3px 8px;font-size:4.4px;color:var(--text);line-height:5px}
.contacts div{display:flex;gap:3px;align-items:flex-start}
.contacts svg{flex:none}
.card-back{top:783px;height:102px}
.card-back .frame{left:6px;top:8px;right:6px;bottom:17px}
.card-back .band{height:17px;font-size:7.5px;justify-content:center}

/* compliment slip */
.slip{left:265px;top:672px;width:432px;height:208px}
.slip .frame{left:10px;top:10px;right:10px;bottom:22px}
.slip .band{height:22px;font-size:12.5px;padding-right:26px}

/* envelope */
.envelope{left:736px;top:671px;width:432px;height:209px}
.flap{position:absolute;left:0;top:0;width:100%;height:72px;background:var(--band);border-radius:0 0 42px 42px;color:#fff;font-size:15.5px;letter-spacing:.08em;display:flex;align-items:center;justify-content:center}
</style>
</head>
<body>

<!-- Letterhead with letter -->
<section class="piece letterhead" aria-label="Letterhead">
  <div class="frame"></div>
  <div class="brand" style="left:36px;top:56px">
    <span class="brand-dot" style="width:18px;height:18px"></span>
    <span class="brand-text"><b style="font-size:13px">Brenmoor</b><i style="font-size:5.2px">Security Services Ltd.</i></span>
  </div>
  <div class="letter">
    <p>July 2, 2012</p>
    <p><strong>Dear Client,</strong><br>ABC Building, def St., Country Name</p>
    <p class="gap">We are pleased to confirm our security services for your premises. Our trained officers provide round-the-clock patrols, access control and alarm response. Each assignment is planned with care and reviewed by our senior team. We keep clear records and report every incident on the same day. Our aim is to protect your people, property and name with discipline.</p>
    <p class="gap">Please find attached our proposed schedule and terms for your review and approval before the agreed start date.</p>
    <p>Our officers are vetted, licensed and trained to the highest standard, and every site receives a dedicated supervisor. We review each contract every quarter and adjust cover as your needs change. Should you have any questions about this proposal, our office team is ready to help at any hour of the day.</p>
    <p>Best Regards,</p>
    <div class="signature" role="img" aria-label="Handwritten signature"></div>
    <p><strong>Daniel Hart</strong><br>Director<br><br>ABC Building, def St., Country Name</p>
  </div>
  <div class="band">
    <svg width="120" height="27" viewBox="0 0 120 27" aria-hidden="true"><polygon points="0,19 108,19 120,27 0,27" fill="#b4b4b4"/></svg>
    <span>www.brenmoorsecurity.com</span>
  </div>
</section>

<!-- Blank sheet -->
<section class="piece sheet" aria-label="Second sheet">
  <div class="frame"></div>
  <div class="brand" style="left:178px;top:262px">
    <span class="brand-dot" style="width:22px;height:22px"></span>
    <span class="brand-text"><b style="font-size:16px">Brenmoor</b><i style="font-size:6.3px">Security Services Ltd.</i></span>
  </div>
  <div class="band"><span>www.brenmoorsecurity.com</span></div>
</section>

<!-- Business card front -->
<section class="piece card card-front" aria-label="Business card front">
  <div class="frame"></div>
  <div class="brand" style="left:12px;top:16px;gap:4px">
    <span class="brand-dot" style="width:10px;height:10px"></span>
    <span class="brand-text"><b style="font-size:8px">Brenmoor</b><i style="font-size:3.3px">Security Services Ltd.</i></span>
  </div>
  <div class="card-name">Owen Blake<small>Production engineer</small></div>
  <div class="contacts">
    <div><svg width="6" height="6" aria-hidden="true"><rect width="6" height="6" fill="#bbb"/></svg>012 345 6789</div>
    <div><svg width="6" height="6" aria-hidden="true"><rect width="6" height="6" fill="#bbb"/></svg>24 Main Road<br>London N1 2AB</div>
    <div><svg width="6" height="6" aria-hidden="true"><rect width="6" height="6" fill="#bbb"/></svg>info@brenmoor.com</div>
    <div><svg width="6" height="6" aria-hidden="true"><rect width="6" height="6" fill="#bbb"/></svg>www.brenmoorsecurity.com</div>
  </div>
  <div class="band">
    <svg width="60" height="9" viewBox="0 0 60 9" aria-hidden="true"><polygon points="0,5 54,5 60,9 0,9" fill="#b4b4b4"/></svg>
  </div>
</section>

<!-- Business card back -->
<section class="piece card card-back" aria-label="Business card back">
  <div class="frame"></div>
  <div class="brand" style="left:52px;top:34px;gap:4px">
    <span class="brand-dot" style="width:11px;height:11px"></span>
    <span class="brand-text"><b style="font-size:9px">Brenmoor</b><i style="font-size:3.6px">Security Services Ltd.</i></span>
  </div>
  <div class="band"><span>www.brenmoorsecurity.com</span></div>
</section>

<!-- Compliment slip -->
<section class="piece slip" aria-label="Compliment slip">
  <div class="frame"></div>
  <div class="brand" style="left:18px;top:38px">
    <span class="brand-dot" style="width:16px;height:16px"></span>
    <span class="brand-text"><b style="font-size:12px">Brenmoor</b><i style="font-size:4.8px">Security Services Ltd.</i></span>
  </div>
  <div class="band">
    <svg width="120" height="22" viewBox="0 0 120 22" aria-hidden="true"><polygon points="0,0 108,0 120,10 0,10" fill="#b4b4b4"/></svg>
    <span>www.brenmoorsecurity.com</span>
  </div>
</section>

<!-- Envelope -->
<section class="piece envelope" aria-label="Envelope">
  <div class="flap">www.brenmoorsecurity.com</div>
  <div class="brand" style="left:163px;top:116px">
    <span class="brand-dot" style="width:20px;height:20px"></span>
    <span class="brand-text"><b style="font-size:14px">Brenmoor</b><i style="font-size:5.6px">Security Services Ltd.</i></span>
  </div>
</section>

</body>
</html>
```